High profile consulting company needs a Business Card Design

I need a business card design for a coaching /consulting company. We specialize in changing behaviors. Our services include therapy, workshops, life coaching, etc.

Check out our website to get a feel for our personality. www.oakbridgeadvisory.com

The new logo will be attached to the website soon, I have attached the new logo for your use on the business card.
Updates

I forgot to provide you with the company email under the "must have" section for the business card.  The website is:

 www.oakbridgeadvisory.com

I understand there's some trouble with the logo I uploaded.  I will try that again.  Thank you for your efforts.

Dana

Thank you for some of your questions.  I prefer a one sided business card, and tend to like the white backgrounds.

I also made 2 small changes to the content.  

add MFT after the name:  Dana Holloway, MFT

and the tag line needed more clarity once I saw it.  Please change it to:  Improving performance by strengthening relationships and changing behaviors.

Thank you,
Dana

Industry/Entity Type

Business

Requirements
Must have
• logo
Phone number: 415-207-5146
email: Dana@oakbridgeadvisory.com
Dana Holloway, MFT
President
Nice to have
• Improving performance by strengthening relationships and changing behaviors.

```html
<!DOCTYPE html>
<html lang="en">
<head>
<meta charset="utf-8">
<title>Oakbridge Advisory – Business Cards</title>
<link rel="stylesheet" href="https://fonts.googleapis.com/css2?family=Arimo:wght@400;700&display=swap">
<style>
  :root {
    --backdrop: #2a2a2c;
    --card: #ffffff;
    --green: #1f7a55;
    --green-deep: #17684a;
    --ink: #2b2b2b;
    --band: #1a1a1a;
    --faint: #e9eeec;
  }
  * { box-sizing: border-box; margin: 0; padding: 0; }
  html, body {
    width: 1200px; height: 944px; overflow: hidden;
    background: var(--backdrop);
    font-family: "Arimo", Arial, sans-serif;
  }
  .stage { position: relative; width: 1200px; height: 944px; }
  .card {
    position: absolute;
    width: 630px; height: 360px;
    background: var(--card);
    border-radius: 22px;
    overflow: hidden;
    box-shadow: 0 12px 30px rgba(0,0,0,.45);
  }
  .card--front { left: 80px; top: 40px; }
  .card--back { left: 400px; top: 470px; }

  .front-decor {
    position: absolute; right: -40px; top: -60px;
    width: 260px; height: 260px; border-radius: 50%;
    background: var(--faint); opacity: .8;
  }
  .brand {
    position: absolute; display: flex; align-items: center; gap: 14px;
  }
  .brand__mark {
    width: 112px; height: 112px; border-radius: 50%;
    border: 10px solid var(--green);
    flex: none;
  }
  .brand__name {
    color: var(--green); font-weight: 700;
    font-size: 44px; line-height: 1; letter-spacing: 1px;
    text-transform: uppercase;
    white-space: nowrap;
  }
  .brand__name span { display: block; letter-spacing: 9px; margin-top: 6px; }
  .card--front .brand { left: 50px; top: 90px; }
  .card--back .brand { left: 34px; top: 54px; transform: scale(.6); transform-origin: left top; }

  .tagline {
    position: absolute; left: 0; right: 0; top: 262px;
    text-align: center; color: var(--ink);
    font-size: 16px; line-height: 1.3;
  }

  .back-panel { position: absolute; inset: 0; }
  .contact {
    position: absolute; left: 34px; top: 250px;
    list-style: none; color: var(--ink); font-size: 16px;
  }
  .contact li { display: flex; align-items: center; gap: 10px; height: 24px; }
  .contact svg { width: 16px; height: 16px; flex: none; }
  .person {
    position: absolute; right: 24px; bottom: 38px;
    text-align: right; color: #fff;
  }
  .person__name { font-size: 26px; }
  .person__title { font-size: 15px; margin-top: 4px; }
</style>
</head>
<body>
<main class="stage">
  <section class="card card--front">
    <div class="front-decor"></div>
    <div class="brand">
      <div class="brand__mark"></div>
      <div class="brand__name">Oakbridge<span>Advisory</span></div>
    </div>
    <p class="tagline">Improving performance by<br>strengthening relationships and changing behaviors.</p>
  </section>

  <section class="card card--back">
    <svg class="back-panel" viewBox="0 0 630 360" width="630" height="360" aria-hidden="true">
      <path d="M400 0 C334 120 312 250 330 360 L356 360 C338 250 360 120 426 0 Z" fill="var(--band)"/>
      <path d="M426 0 C360 120 338 250 356 360 L630 360 L630 0 Z" fill="var(--green)"/>
    </svg>
    <div class="brand">
      <div class="brand__mark"></div>
      <div class="brand__name">Oakbridge<span>Advisory</span></div>
    </div>
    <ul class="contact">
      <li>
        <svg viewBox="0 0 16 16"><path d="M4 1 L6.5 4 L5 6 C6 8 8 10 10 11 L12 9.5 L15 12 L13 15 C7 14 2 9 1 3 Z" fill="var(--green)"/></svg>
        415-207-5146
      </li>
      <li>
        <svg viewBox="0 0 16 16"><rect x="1" y="3" width="14" height="10" rx="1.5" fill="var(--green)"/><path d="M1.5 4 L8 9 L14.5 4" stroke="#fff" stroke-width="1.2" fill="none"/></svg>
        Dana@oakbridgeadvisory.com
      </li>
      <li>
        <svg viewBox="0 0 16 16"><circle cx="8" cy="8" r="7" fill="var(--green)"/><path d="M1 8 H15 M8 1 C4 5 4 11 8 15 M8 1 C12 5 12 11 8 15" stroke="#fff" stroke-width="1" fill="none"/></svg>
        www.oakbridgeadvisory.com
      </li>
    </ul>
    <div class="person">
      <div class="person__name">Dana Holloway</div>
      <div class="person__title">MFT, President</div>
    </div>
  </section>
</main>
</body>
</html>
```